Quillbrookes websites redesign

Www.quill-brookes.com needs to be redesigned along with updations. The incremental material will be provided for the updations. We are looking for complete redesign of the pages with the new content. The complete write up will be provided soon

Target Market(s)

Global

Coding

Coded - Design and coding required

Number of Pages Required

5+ page

Requirements
Must have
• A clean and slick design for the Consulting.
Should not have
• Too many pictures which reduces the speed of the site

```html
<!DOCTYPE html>
<html lang="en">
<head>
<meta charset="utf-8">
<title>Quillbrookes Consultancy</title>
<link href="https://fonts.googleapis.com/css2?family=Raleway:wght@400;500;600;700&family=Open+Sans:ital,wght@0,400;0,600;0,700;1,400;1,600&display=swap" rel="stylesheet">
<style>
:root{
  --blue:#3aa0c9;
  --ink:#1f2430;
  --body:#666;
  --maroon:#5a1d22;
  --grey:#f2f2f2;
  --line:#dcdcdc;
  --footer:#333333;
  --footer-text:#e6e6e6;
}
*{box-sizing:border-box;margin:0;padding:0}
html,body{width:1200px;height:2550px;overflow:hidden;background:#fff}
body{position:relative;font-family:'Open Sans',sans-serif;color:var(--ink)}
.abs{position:absolute}

.topline{left:0;top:0;width:1200px;height:5px;background:var(--blue)}
.header{left:0;top:5px;width:1200px;height:83px;background:#fff}
.brand{left:99px;top:24px;display:flex;align-items:center;gap:12px}
.brand-dot{width:40px;height:40px;border-radius:50%;background:var(--maroon)}
.brand-name{font-family:'Raleway',sans-serif;font-weight:500;font-size:34px;color:var(--ink)}
.nav{top:36px;font-family:'Raleway',sans-serif;font-weight:500;font-size:15px;color:var(--ink)}
.nav.active{color:var(--blue)}
.search{left:1062px;top:27px;width:38px;height:38px;border-radius:50%;background:var(--maroon)}

.hero{left:0;top:88px;width:1200px;height:434px;background:linear-gradient(120deg,#b9c6d2 0%,#7f93a8 45%,#3f4f63 100%)}
.hero-title{left:0;top:258px;width:1200px;text-align:center;font-family:'Raleway',sans-serif;font-weight:500;font-size:64px;color:#fff;text-shadow:0 2px 6px rgba(0,0,0,.35)}
.dots{left:566px;top:472px;display:flex;gap:4px}
.dots span{width:15px;height:15px;border-radius:50%;border:2px solid #fff}
.dots span.on{background:var(--blue)}

.section-title{left:0;width:1200px;text-align:center;font-family:'Raleway',sans-serif;font-weight:600;font-size:22px;color:var(--ink)}
.meter{width:170px;height:170px}
.meter-label{width:170px;text-align:center;font-family:'Open Sans',sans-serif;font-weight:700;font-size:25px;color:var(--ink)}

.welcome-art{left:0;top:831px;width:601px;height:436px;background:linear-gradient(135deg,#52b6de,#2e93c4)}
.welcome-panel{left:601px;top:831px;width:599px;height:436px;background:var(--grey)}
.block-title{font-family:'Raleway',sans-serif;font-weight:600;font-size:22px;color:var(--ink)}
.copy{font-size:12.5px;line-height:25.5px;color:var(--body)}
.more{font-family:'Raleway',sans-serif;font-weight:700;font-size:13px;color:var(--maroon)}

.subtitle{left:0;width:1200px;text-align:center;font-style:italic;font-weight:600;font-size:13.5px;color:var(--blue)}
.card{width:240px;height:162px;border:1px solid var(--line);padding:5px;background:#fff}
.card-img{width:100%;height:100%}
.card-caption{width:240px;text-align:center;font-family:'Raleway',sans-serif;font-weight:600;font-size:14.5px;line-height:23px;color:var(--ink)}

.founder-band{left:0;top:1680px;width:1200px;height:352px;background:var(--grey)}
.founder-photo{left:99px;top:1680px;width:302px;height:352px;background:linear-gradient(160deg,#8a5a3a,#3a2a2e 55%,#1e1a22)}

.partner{top:2081px;width:185px;height:89px;border:1px solid var(--line);display:flex;align-items:center;justify-content:center;font-family:'Raleway',sans-serif;font-weight:600;font-size:24px;color:#2b4a7a}

.footer{left:0;top:2215px;width:1200px;height:335px;background:var(--footer)}
.f-head{top:2247px;font-family:'Raleway',sans-serif;font-weight:700;font-size:15px;color:#fff}
.f-list{list-style:none;font-size:12px;color:var(--footer-text)}
.f-list li{height:25px}
.f-text{font-size:12px;line-height:20px;color:var(--footer-text)}
.email{left:287px;top:2290px;width:300px;height:33px;background:#fff;font-size:12px;color:#888;padding:8px 12px}
.subscribe{left:287px;top:2335px;width:97px;height:34px;background:var(--blue);border:2px solid #fff;font-weight:700;font-size:11px;color:#fff;text-align:center;line-height:30px}
.f-sep{top:2248px;width:1px;height:140px;background:#444}
.contact-row{left:878px;display:flex;gap:18px;font-size:12px;line-height:16px;color:var(--footer-text)}
.contact-row svg{flex:none;margin-top:1px}
.f-brand{left:94px;top:2489px;display:flex;align-items:center;gap:10px}
.f-brand .brand-dot{width:32px;height:32px;background:#fff}
.f-brand .brand-name{font-size:25px;color:#fff}
.copyright{left:0;top:2498px;width:1200px;text-align:center;font-size:12px;color:var(--footer-text)}
.social{top:2489px;width:37px;height:37px;border:2px solid #fff;border-radius:50%}
</style>
</head>
<body>

<div class="abs topline"></div>
<header class="abs header">
  <div class="abs brand" style="top:19px"><span class="brand-dot"></span><span class="brand-name">Quillbrookes</span></div>
  <span class="abs nav active" style="left:487px;top:31px">Home</span>
  <span class="abs nav" style="left:557px;top:31px">Founder</span>
  <span class="abs nav" style="left:644px;top:31px">Consultancy</span>
  <span class="abs nav" style="left:758px;top:31px">System</span>
  <span class="abs nav" style="left:840px;top:31px">Case Studies</span>
  <span class="abs nav" style="left:958px;top:31px">Contact Us</span>
  <div class="abs search">
    <svg width="38" height="38" viewBox="0 0 38 38"><circle cx="17" cy="17" r="6" fill="none" stroke="#fff" stroke-width="2.5"/><line x1="21.5" y1="21.5" x2="26" y2="26" stroke="#fff" stroke-width="3" stroke-linecap="round"/></svg>
  </div>
</header>

<section class="abs hero" role="img" aria-label="Hand touching a glowing network of connected business icons"></section>
<h1 class="abs hero-title">Global Trade Council</h1>
<div class="abs dots"><span class="on"></span><span></span><span></span><span></span></div>

<h2 class="abs section-title" style="top:562px">World Merchandising Trade 2012 ( USD Billion)</h2>
<svg class="abs meter" style="left:138px;top:619px" viewBox="0 0 170 170"><circle cx="85" cy="85" r="80" fill="none" stroke="#222" stroke-width="1.5"/><circle cx="85" cy="85" r="80" fill="none" stroke="#3aa0c9" stroke-width="6" stroke-dasharray="200 503" transform="rotate(-70 85 85)"/></svg>
<div class="abs meter-label" style="left:138px;top:686px">0 - 250</div>
<svg class="abs meter" style="left:389px;top:619px" viewBox="0 0 170 170"><circle cx="85" cy="85" r="80" fill="none" stroke="#222" stroke-width="1.5"/><circle cx="85" cy="85" r="80" fill="none" stroke="#3aa0c9" stroke-width="6" stroke-dasharray="380 503" transform="rotate(30 85 85)"/></svg>
<div class="abs meter-label" style="left:389px;top:686px">250 - 500</div>
<svg class="abs meter" style="left:641px;top:619px" viewBox="0 0 170 170"><circle cx="85" cy="85" r="80" fill="none" stroke="#222" stroke-width="1.5"/><circle cx="85" cy="85" r="80" fill="none" stroke="#3aa0c9" stroke-width="6" stroke-dasharray="320 503" transform="rotate(-80 85 85)"/></svg>
<div class="abs meter-label" style="left:641px;top:686px">500 - 1000</div>
<svg class="abs meter" style="left:891px;top:619px" viewBox="0 0 170 170"><circle cx="85" cy="85" r="80" fill="none" stroke="#222" stroke-width="1.5"/><circle cx="85" cy="85" r="80" fill="none" stroke="#3aa0c9" stroke-width="6" stroke-dasharray="140 503" transform="rotate(140 85 85)"/></svg>
<div class="abs meter-label" style="left:891px;top:686px">&gt; 1000</div>

<div class="abs welcome-art" role="img" aria-label="Illustrated world map with business people, charts and strategy sketches on blue"></div>
<div class="abs welcome-panel"></div>
<h2 class="abs block-title" style="left:649px;top:870px">Welcome to Quillbrookes</h2>
<p class="abs copy" style="left:653px;top:918px;width:455px">Quillbrookes Consultancy Limited capitalizes on synergies arising from trade and investment linkages between countries and knowledge of traditional and non-traditional pools of liquidity to provide consultancy services to Emerging country banks, Corporates and SMEs.</p>
<p class="abs copy" style="left:653px;top:1045px;width:455px">The Consultancy provides bank neutral views to Corporates and SMEs in Asian emerging markets and helps in improving financial structure and efficient use of funds. Our endeavor is to provide a distinct bottom line advantage to our clients. The primary focus is in regionalisation of the banking relationship across the globe, providing structured finance solutions and off balance sheet solutions.</p>
<span class="abs more" style="left:651px;top:1200px">READ MORE &gt;&gt;</span>

<h2 class="abs section-title" style="top:1308px">Case Studies</h2>
<p class="abs subtitle" style="top:1348px">Some of the deals completed by QCL are summarised below to describe the range of activities undertaken with Corporates</p>
<div class="abs card" style="left:98px;top:1406px"><div class="card-img" role="img" aria-label="Businessman facing a rising city skyline" style="background:linear-gradient(180deg,#e6eef6,#7fa6c9)"></div></div>
<div class="abs card" style="left:353px;top:1406px"><div class="card-img" role="img" aria-label="Businessman with tablet over a grey world map" style="background:linear-gradient(90deg,#e9e9e9,#8c8f95)"></div></div>
<div class="abs card" style="left:608px;top:1406px"><div class="card-img" role="img" aria-label="Hands holding a glowing group of people figures" style="background:linear-gradient(180deg,#1c3550,#2c6e9b 60%,#0f1c2a)"></div></div>
<div class="abs card" style="left:862px;top:1406px"><div class="card-img" role="img" aria-label="Businessman working at a laptop with charts behind" style="background:linear-gradient(90deg,#f1f1ee,#c9cfd6)"></div></div>
<div class="abs card-caption" style="left:98px;top:1585px">Export Credit Agency backed<br>long term Project financing</div>
<div class="abs card-caption" style="left:353px;top:1585px">Structured Financing</div>
<div class="abs card-caption" style="left:608px;top:1585px">Local banks for International<br>Subsidiary Banking</div>
<div class="abs card-caption" style="left:862px;top:1585px">Bank Lines Business</div>

<div class="abs founder-band"></div>
<div class="abs founder-photo" role="img" aria-label="Founder speaking at a podium with flowers at a conference"></div>
<h2 class="abs block-title" style="left:459px;top:1717px">Meera Kapoor</h2>
<p class="abs copy" style="left:463px;top:1762px;width:645px">Ms. Meera Kapoor is the founder director of Quillbrookes Consultancy Limited (QCL) based at Hong Kong. Meera worked as the Alternate Chief Executive of Northgate Bank, Hong Kong Branch until Jan 2013, heading Corporate Banking business in North Asia and Export Credit Agency business globally. During her tenure, both the businesses increased multifold.</p>
<p class="abs copy" style="left:463px;top:1891px;width:645px">Meera started her banking career with Northgate Bank Ltd, India's second largest bank in the year 2002 and in the next 10 years handled multiple leadership responsibilities in the Corporate.</p>
<span class="abs more" style="left:463px;top:1970px">READ MORE &gt;&gt;</span>

<div class="abs partner" style="left:98px">Swiftly</div>
<div class="abs partner" style="left:302px">Envoyra</div>
<div class="abs partner" style="left:506px">Varenta</div>
<div class="abs partner" style="left:712px">SkyReady</div>
<div class="abs partner" style="left:918px">StudyWorks</div>

<footer class="abs footer"></footer>
<h3 class="abs f-head" style="left:99px">INFORMATION</h3>
<ul class="abs f-list" style="left:99px;top:2284px">
  <li>Home</li><li>Founder</li><li>Consultancy</li><li>System</li><li>Case Studies</li><li style="margin-top:5px">Contact Us</li>
</ul>
<div class="abs f-sep" style="left:255px"></div>
<h3 class="abs f-head" style="left:287px">NEWSLETTER SUBSCRIPTION</h3>
<p class="abs f-text" style="left:287px;top:2283px;width:300px">Register your email address to get information about us</p>
<div class="abs email" style="top:2341px">Email Address</div>
<div class="abs subscribe" style="top:2386px">SUBSCRIBE</div>
<div class="abs f-sep" style="left:648px"></div>
<h3 class="abs f-head" style="left:682px">QUICK LINKS</h3>
<ul class="abs f-list" style="left:682px;top:2284px">
  <li>Query</li><li>Help</li><li>FAQ</li><li>Privacy Policy</li><li>Terms &amp; Conditions</li><li>System</li>
</ul>
<div class="abs f-sep" style="left:828px"></div>
<h3 class="abs f-head" style="left:878px">CONTACT US</h3>
<div class="abs contact-row" style="top:2288px">
  <svg width="11" height="15" viewBox="0 0 11 15"><path d="M5.5 0C2.5 0 0 2.4 0 5.4 0 9.4 5.5 15 5.5 15S11 9.4 11 5.4C11 2.4 8.5 0 5.5 0z" fill="#fff"/><circle cx="5.5" cy="5.3" r="2" fill="#333"/></svg>
  <span style="width:250px">Suite 04, 9th Floor, Harbourline Tower, 18 Marlow Road East, Kowloon, Hong Kong</span>
</div>
<div class="abs contact-row" style="top:2356px">
  <svg width="12" height="12" viewBox="0 0 12 12"><path d="M2.4 0.5l2 2.3-1.2 1.6c.8 1.7 2.1 3 3.8 3.8l1.6-1.2 2.3 2-1.2 2.3C4.6 11 1 7.4.3 2.3z" fill="#fff"/></svg>
  <span>+852-2000 4175</span>
</div>
<div class="abs contact-row" style="top:2382px">
  <svg width="12" height="13" viewBox="0 0 12 13"><rect x="0" y="4" width="12" height="9" rx="1" fill="#fff"/><rect x="2.5" y="0" width="7" height="5" fill="#fff"/><rect x="3" y="7" width="6" height="1.5" fill="#333"/><rect x="3" y="9.5" width="6" height="1.5" fill="#333"/></svg>
  <span>+852-2000 4176</span>
</div>
<div class="abs contact-row" style="top:2410px">
  <svg width="13" height="10" viewBox="0 0 13 10"><rect width="13" height="10" rx="1" fill="#fff"/><path d="M0.5 0.8l6 4.6 6-4.6" fill="none" stroke="#333" stroke-width="1.2"/></svg>
  <span>query@quill-brookes.com</span>
</div>

<div class="abs f-brand"><span class="brand-dot"></span><span class="brand-name">Quillbrookes</span></div>
<p class="abs copyright">Copyrights © 2016, Quill - Brookes. All rights reserved.</p>
<div class="abs social" style="left:936px"></div>
<div class="abs social" style="left:978px"></div>
<div class="abs social" style="left:1020px"></div>
<div class="abs social" style="left:1063px"></div>

</body>
</html>
```